mobile physiotherapy for the elderly

i have include a logo for you to use
i have included important info to include on the flyer.
the flyer will be a dl size
the flyer will be used for getting new clients at a health expo. it needs to be eye catching as i may be using it as a vertical banner at my stall
big words and illustations that take up most of the design

Target Market(s)

veterans of war, mainly over 55years of age

Industry/Entity Type

Healthcare

Font styles to use
Sans Serif
Decorative
Script
Other font styles liked:
• i would like the slogan in a handwriting type font, but not running-writing or overly formal fonts

Colors

Designer to choose colors to be used in the design.

Requirements
Must have
• i would like to incorporate my logo woth the slogan " we come to you!" i want this slogan to be very prominent as i may want to use this as a vertical banner at a health expo
• i would like to see an illustrated (Cartoon-like) car on one side and a house on the other, being joined together by a winding road.
Nice to have
• potentially something with a map in the background or as the background or the whole flyer. We are located and work in sydney, australia. so if you can tastefully include a map that would be great. it does not need to be a map of sydney if you dont feel like it works
Should not have
• no photographs
• no people

```html
<!DOCTYPE html>
<html lang="en">
<head>
<meta charset="utf-8">
<title>Hearth Physiotherapy – DL Flyer</title>
<link rel="stylesheet" href="https://fonts.googleapis.com/css2?family=Raleway:wght@700;800&family=Open+Sans:wght@400;600&display=swap">
<style>
  :root {
    --navy: #4a5a8f;
    --ink: #555a60;
    --sky-top: #f5f9fb;
    --sky-bottom: #c3e8e6;
    --road: #516a77;
    --accent: #6cc0e6;
    --white: #ffffff;
    --stage: #e9ecee;
  }
  * { box-sizing: border-box; margin: 0; padding: 0; }
  html, body { width: 1200px; height: 1200px; overflow: hidden; }
  body { background: var(--stage); position: relative; font-family: "Open Sans", Arial, sans-serif; }

  .flyer {
    position: absolute; top: 143px; width: 476px; height: 952px;
    background: linear-gradient(to bottom, var(--sky-top) 0%, var(--sky-top) 62%, var(--sky-bottom) 86%);
    overflow: hidden; text-align: center; color: var(--ink);
  }
  .flyer--front { left: 101px; }
  .flyer--back { left: 614px; }

  .abs { position: absolute; left: 0; right: 0; }

  .brand { display: flex; flex-direction: column; align-items: center; color: var(--navy); font-family: "Raleway", sans-serif; font-weight: 700; }
  .brand__row { display: flex; align-items: center; gap: 14px; }
  .brand__name { font-size: 60px; letter-spacing: 2px; line-height: 1; }
  .brand__dot { width: 38px; height: 38px; border-radius: 50%; background: var(--navy); }
  .brand__sub { font-size: 19px; letter-spacing: 12px; margin-top: 12px; padding-left: 12px; }

  .headline { font-family: "Raleway", sans-serif; font-weight: 800; color: var(--navy); letter-spacing: -1px; }
  .slogan { top: 218px; font-size: 41px; }
  .evaluate { top: 290px; font-size: 23px; font-weight: 600; line-height: 27px; }
  .specialised { top: 403px; font-size: 38px; }
  .specialised-note { top: 450px; font-size: 24px; line-height: 27px; }
  .one-on-one { top: 540px; font-size: 25px; line-height: 30px; }
  .one-on-one strong { font-weight: 600; }

  .scene { position: absolute; left: 0; right: 0; }
  .scene--town { top: 617px; height: 200px; background: linear-gradient(to bottom, rgba(195,232,230,0) 0%, #b3dcd8 50%, #a9c7c9 100%); }
  .scene--car { top: 720px; height: 97px; left: 240px; right: 40px; background: linear-gradient(to bottom, rgba(195,232,230,0), #b7d4dc); border-radius: 30px 30px 0 0; }

  .road { position: absolute; left: 0; right: 0; bottom: 0; height: 135px; background: var(--road); color: var(--white); }
  .road__dashes { position: absolute; left: 0; width: 100%; height: 4px; }
  .road__call { position: absolute; left: 0; right: 0; top: 13px; font-size: 21px; letter-spacing: 0.3px; }
  .road__phone { position: absolute; left: 0; right: 0; top: 60px; font-family: "Raleway", sans-serif; font-weight: 800; font-size: 50px; letter-spacing: -1px; }
  .road__web { position: absolute; left: 0; right: 0; top: 64px; font-size: 36px; }

  .help-title { top: 60px; font-size: 38px; text-align: left; left: 48px; }
  .help-list { position: absolute; top: 112px; left: 48px; list-style: none; text-align: left; }
  .help-list li { display: flex; align-items: center; gap: 12px; font-size: 24px; height: 38px; color: var(--ink); }
  .help-list svg { width: 20px; height: 20px; flex: none; }

  .back-brand { top: 410px; }
  .back-call { top: 612px; font-size: 21px; color: var(--navy); }
  .back-phone { top: 640px; font-size: 52px; }
</style>
</head>
<body>
  <section class="flyer flyer--front" aria-label="Flyer front">
    <div class="abs brand" style="top:52px">
      <div class="brand__row"><span class="brand__name">HEARTH</span><span class="brand__dot"></span></div>
      <div class="brand__sub">PHYSIOTHERAPY</div>
    </div>
    <h1 class="abs headline slogan">WE COME TO YOU!</h1>
    <p class="abs evaluate">TRAINED AND EXPERIENCED<br>PROFESSIONALS EVALUATE YOUR<br>REHABILITATION NEEDS</p>
    <h2 class="abs headline specialised">SPECIALISED</h2>
    <p class="abs specialised-note">treatment programs to suit<br>individual needs</p>
    <p class="abs one-on-one"><strong>ONE-ON-ONE PHYSIOTHERAPY</strong><br>TREATMENT IN YOUR HOME</p>
    <div class="scene scene--town" role="img" aria-label="Illustrated street of colourful houses, apartment blocks, a tree and a supermarket under soft clouds"></div>
    <div class="road">
      <p class="road__call">CALL US FOR FURTHER INFORMATION</p>
      <svg class="road__dashes" style="top:50px" viewBox="0 0 476 4" preserveAspectRatio="none"><line x1="0" y1="2" x2="476" y2="2" stroke="#fff" stroke-width="3" stroke-dasharray="28 18"/></svg>
      <p class="road__phone">0400 123 456</p>
    </div>
  </section>

  <section class="flyer flyer--back" aria-label="Flyer back">
    <h2 class="abs headline help-title">HOW WE CAN HELP:</h2>
    <ul class="help-list">
      <li><svg viewBox="0 0 20 20"><circle cx="10" cy="10" r="9" fill="var(--accent)"/><path d="M5 10h9M10 6l4 4-4 4" stroke="#fff" stroke-width="2" fill="none"/></svg>Post-surgical Rehabilitation</li>
      <li><svg viewBox="0 0 20 20"><circle cx="10" cy="10" r="9" fill="var(--accent)"/><path d="M5 10h9M10 6l4 4-4 4" stroke="#fff" stroke-width="2" fill="none"/></svg>Geriatric Care</li>
      <li><svg viewBox="0 0 20 20"><circle cx="10" cy="10" r="9" fill="var(--accent)"/><path d="M5 10h9M10 6l4 4-4 4" stroke="#fff" stroke-width="2" fill="none"/></svg>Postural Analysis</li>
      <li><svg viewBox="0 0 20 20"><circle cx="10" cy="10" r="9" fill="var(--accent)"/><path d="M5 10h9M10 6l4 4-4 4" stroke="#fff" stroke-width="2" fill="none"/></svg>Neurological Disorders</li>
      <li><svg viewBox="0 0 20 20"><circle cx="10" cy="10" r="9" fill="var(--accent)"/><path d="M5 10h9M10 6l4 4-4 4" stroke="#fff" stroke-width="2" fill="none"/></svg>Aid prescription</li>
      <li><svg viewBox="0 0 20 20"><circle cx="10" cy="10" r="9" fill="var(--accent)"/><path d="M5 10h9M10 6l4 4-4 4" stroke="#fff" stroke-width="2" fill="none"/></svg>Pain management</li>
    </ul>
    <div class="abs brand back-brand">
      <div class="brand__row"><span class="brand__name">HEARTH</span><span class="brand__dot"></span></div>
      <div class="brand__sub">PHYSIOTHERAPY</div>
    </div>
    <p class="abs back-call">CALL US FOR FURTHER INFORMATION</p>
    <p class="abs headline back-phone">0400 123 456</p>
    <div class="scene scene--car" role="img" aria-label="Illustrated white car with luggage on the roof rack driving along the road"></div>
    <div class="road">
      <svg class="road__dashes" style="top:32px" viewBox="0 0 476 4" preserveAspectRatio="none"><line x1="0" y1="2" x2="476" y2="2" stroke="#fff" stroke-width="3" stroke-dasharray="28 30"/></svg>
      <p class="road__web">www.website.com</p>
    </div>
  </section>
</body>
</html>
```